Equipment Finance Specialist I work with companies who need the funds to buy their equipment

I would like a business card that stands out on the shelves. I want to be able to hand it to someone and say WOW. This card should have my logo.
You can put color into it I am very open on design and color

What my company does is we deal with dealerships that sell equipment such as Dump Trucks garbage trucks tractors trailers. Customers get referred to us and depending on their time in business we will ask for the following items

Companies that have been in business for more than two years we have a credit application program up to 250K . With this program we need the following items Credit application filled out(which is what I would like to be able for the customer to click on my website to get.) as well as three current month bank statements.

Deals over 250k we will need the following items

2 years business tax returns
2 years personal tax returns
Profit & Loss statement
Personal Financial Statement

what we do
100% FINANCING
SEASONAL PAYMENTS
LOAN BALLOON PAYMENTS
TRAC LEASING
LOW-INTEREST REFINANCING RATES
DEBT CONSOLIDATION

We specialize in creative financing solutions and offer a variety of reliable, flexible and expandable lending choices.

Target Market(s)

Trucking Companies

Industry/Entity Type

Trucking Company

Contact Information for Business Card

* $250,000 Application only Program
* Loans from $30,000 to 5,000,000
* Competitive Interest Rates

Font styles to use
Serif
Sans Serif

Colors

Designer to choose colors to be used in the design.

Requirements
Must have
• On the back of the card.
• * $250,000 Application only Program
• * Loans from $30,000 to 5,000,000
• My name, email, website. address
• * Competitive Interest Rates
• * 100% Financing
Nice to have
• I want my logo to pop on the card
• My logo is the great one I would like to use
Should not have
• I am up for your creativity as well

```html
<!DOCTYPE html>
<html lang="en">
<head>
<meta charset="UTF-8">
<title>Summit Haul — Business Card</title>
<link rel="stylesheet" href="https://fonts.googleapis.com/css2?family=Oswald:wght@500;600&family=Work+Sans:wght@400;500&display=swap">
<style>
  :root {
    --backdrop: #1c1c1d;
    --card-dark: #161617;
    --card-light: #2b2b2c;
    --brand-green: #6cb33f;
    --text-white: #f2f2f2;
    --text-soft: #c9c9c9;
  }
  * { box-sizing: border-box; margin: 0; padding: 0; }
  html, body {
    width: 1200px;
    height: 900px;
    overflow: hidden;
    background: var(--backdrop);
  }
  .canvas {
    position: relative;
    width: 1200px;
    height: 900px;
    display: flex;
    flex-direction: column;
    align-items: center;
    justify-content: center;
    gap: 40px;
  }
  .card {
    position: relative;
    width: 660px;
    height: 377px;
    background: linear-gradient(135deg, var(--card-dark) 0%, #1e1e1f 55%, var(--card-light) 100%);
    overflow: hidden;
  }
  .card::after {
    content: "";
    position: absolute;
    left: 0; right: 0; bottom: 0;
    height: 6px;
    background: var(--brand-green);
  }

  /* Front */
  .card-front {
    display: flex;
    align-items: center;
    justify-content: center;
  }
  .brand-lockup {
    display: flex;
    align-items: center;
    gap: 16px;
    margin-bottom: 20px;
  }
  .brand-dot {
    width: 54px;
    height: 54px;
    border-radius: 50%;
    background: var(--brand-green);
  }
  .brand-name {
    font-family: "Oswald", sans-serif;
    font-weight: 600;
    font-size: 58px;
    letter-spacing: 2px;
    color: var(--brand-green);
    text-transform: uppercase;
  }

  /* Back */
  .program-list {
    position: absolute;
    left: 40px;
    right: 40px;
    top: 40px;
    list-style: none;
    display: grid;
    grid-template-columns: 1fr 1fr;
    row-gap: 10px;
    column-gap: 24px;
    font-family: "Work Sans", sans-serif;
    font-size: 14px;
    color: var(--text-soft);
    letter-spacing: 0.4px;
  }
  .program-item {
    display: flex;
    align-items: center;
    gap: 10px;
    white-space: nowrap;
  }
  .program-item::before {
    content: "";
    width: 7px;
    height: 7px;
    flex: none;
    background: var(--brand-green);
  }
  .person {
    position: absolute;
    right: 392px;
    top: 146px;
    text-align: right;
  }
  .person-name {
    font-family: "Oswald", sans-serif;
    font-weight: 500;
    font-size: 40px;
    line-height: 1;
    color: var(--brand-green);
    text-transform: uppercase;
    letter-spacing: 0.5px;
    white-space: nowrap;
  }
  .person-title {
    font-family: "Work Sans", sans-serif;
    font-size: 16px;
    color: var(--text-white);
    margin-top: 6px;
    letter-spacing: 0.5px;
  }
  .divider {
    position: absolute;
    left: 290px;
    top: 158px;
    width: 2px;
    height: 60px;
    background: var(--text-white);
  }
  .contact-list {
    position: absolute;
    left: 316px;
    top: 156px;
    list-style: none;
    font-family: "Work Sans", sans-serif;
    font-size: 17px;
    color: var(--text-white);
    letter-spacing: 0.5px;
  }
  .contact-item {
    display: flex;
    align-items: center;
    gap: 12px;
    height: 23px;
    white-space: nowrap;
  }
  .contact-icon {
    width: 12px;
    height: 12px;
    flex: none;
  }
  .accent { color: var(--brand-green); }
  .address {
    position: absolute;
    left: 40px;
    bottom: 46px;
    font-family: "Work Sans", sans-serif;
    font-size: 18px;
    color: var(--text-white);
    letter-spacing: 0.8px;
  }
</style>
</head>
<body>
<main class="canvas">
  <section class="card card-front">
    <div class="brand-lockup">
      <span class="brand-dot"></span>
      <span class="brand-name">Summit Haul</span>
    </div>
  </section>

  <section class="card card-back">
    <ul class="program-list">
      <li class="program-item">$250,000 Application Only Program</li>
      <li class="program-item">Loans from $30,000 to $5,000,000</li>
      <li class="program-item">Competitive Interest Rates</li>
      <li class="program-item">100% Financing</li>
    </ul>
    <div class="person">
      <h1 class="person-name">Daniel Reyes</h1>
      <p class="person-title">Director</p>
    </div>
    <span class="divider"></span>
    <ul class="contact-list">
      <li class="contact-item">
        <svg class="contact-icon" viewBox="0 0 12 12"><path d="M2.5 1 L4.5 1 L5.2 3.6 L4 4.5 C4.6 5.9 6.1 7.4 7.5 8 L8.4 6.8 L11 7.5 L11 9.5 C11 10.3 10.3 11 9.5 11 C5 11 1 7 1 2.5 C1 1.7 1.7 1 2.5 1 Z" fill="var(--brand-green)"/></svg>
        <span>1300 472 615</span>
      </li>
      <li class="contact-item">
        <svg class="contact-icon" viewBox="0 0 12 12"><rect x="0.75" y="2.25" width="10.5" height="7.5" fill="none" stroke="var(--brand-green)" stroke-width="1.3"/><path d="M1 2.6 L6 6.5 L11 2.6" fill="none" stroke="var(--brand-green)" stroke-width="1.3"/></svg>
        <span>info@summithaul.com</span>
      </li>
      <li class="contact-item">
        <svg class="contact-icon" viewBox="0 0 12 12"><circle cx="6" cy="6" r="5.2" fill="none" stroke="var(--brand-green)" stroke-width="1.2"/><ellipse cx="6" cy="6" rx="2.3" ry="5.2" fill="none" stroke="var(--brand-green)" stroke-width="1"/><path d="M0.8 6 H11.2" stroke="var(--brand-green)" stroke-width="1"/></svg>
        <span>www.<span class="accent">summithaul</span>.com</span>
      </li>
    </ul>
    <p class="address">2188 Redfern Ave. Austin, TX 78704</p>
  </section>
</main>
</body>
</html>
```